Networking Events Calendar/Diary

We need a responsive website that can act as both an online diary/calendar and a resource for community and networking events similar to brimtolvenquarrix.com (we do not want a clone, but one with similar functionality). We need to be able to host adverts, have a client area for clients to add their own events to the diary. This needs to have the functionality that clients have to pay to add recurring events. Some integration would be useful so that if a clients already has their own online diary on their website then using an API possibly to also add that event into our online diary

Industry/Entity Type

Events

Coding

Coded - Design and coding required

Number of Pages Required

5+ page

Requirements
Must have
• My project must have a calendar area, space for ads, be responsive and easily viewable on mobile. A subscribers area for clients and a way to purchase premium status so that premium events are highlighted.

```html
<!DOCTYPE html>
<html lang="en">
<head>
<meta charset="utf-8">
<title>Quarrix Diary</title>
<link rel="stylesheet" href="https://fonts.googleapis.com/css2?family=Open+Sans:ital,wght@0,400;0,600;0,700;0,800;1,400&display=swap">
<style>
:root{
  --orange:#f7941d;
  --ink:#222;
  --body:#777;
  --line:#ddd;
  --footer:#111;
  --white:#fff;
}
*{margin:0;padding:0;box-sizing:border-box}
html,body{width:711px;height:1200px;overflow:hidden;background:var(--white)}
body{font-family:"Open Sans",sans-serif;color:var(--ink);position:relative}

.site-header{height:28px;display:flex;align-items:center;padding:0 140px 0 142px;gap:14px}
.brand{font-weight:800;font-size:12px;color:var(--ink);white-space:nowrap;margin-right:8px}
.search{width:70px;height:10px;border:1px solid var(--line);border-radius:5px;font-size:5px;color:#aaa;padding-left:4px;line-height:8px}
.main-nav{display:flex;gap:10px;font-size:5px;font-weight:700;color:var(--ink);margin-left:10px}
.account{display:flex;gap:8px;font-size:5px;font-weight:700;color:var(--orange);margin-left:auto}

.hero{position:relative;height:220px;background:linear-gradient(135deg,#2a0e3a 0%,#5a1830 35%,#b32a2a 60%,#3a1440 100%);text-align:center;color:var(--white)}
.hero-photo{position:absolute;inset:0;background:radial-gradient(ellipse at 75% 30%,rgba(255,170,120,.55),transparent 55%),radial-gradient(ellipse at 50% 100%,rgba(20,10,30,.7),transparent 70%)}
.hero-content{position:relative;padding-top:56px}
.hero h1{font-size:22px;font-weight:800;letter-spacing:.5px}
.hero p{font-size:6px;width:140px;margin:8px auto 0;line-height:9px;color:#eee}
.btn-primary{display:inline-block;margin-top:12px;background:var(--orange);color:var(--white);font-size:5.5px;font-weight:700;padding:4px 18px;border-radius:2px}

.section-title{text-align:center;color:var(--orange);font-size:13px;font-weight:700;letter-spacing:2px}
.events-title{position:absolute;top:279px;left:0;right:0}

.events{position:absolute;top:327px;left:142px;width:427px}
.event-row{display:flex;height:157px}
.event-photo{width:213px;height:100%}
.photo-crowd{background:linear-gradient(160deg,#2a1d5a,#7b3ea8 45%,#1a1230)}
.photo-stage{background:linear-gradient(180deg,#0c1430,#3a4f9a 45%,#d9dff2 60%,#1c2240)}
.photo-banquet{background:linear-gradient(170deg,#4a1a10,#b83a22 50%,#e7c0a0)}
.event-card{width:214px;padding:24px 16px}
.event-card h2{font-size:8px;font-weight:600;color:var(--ink)}
.event-card p{font-size:5px;line-height:8px;color:var(--body);margin-top:8px}
.btn-outline{display:inline-block;margin-top:10px;border:1px solid #999;border-radius:8px;font-size:4.5px;padding:3px 12px;color:#555}

.how-title{position:absolute;top:838px;left:0;right:0}
.testimonial{position:absolute;top:878px;left:150px;width:410px;text-align:center;font-style:italic;font-size:10.5px;line-height:13px;color:#888}
.quote-mark{position:absolute;font-family:Georgia,serif;font-size:58px;font-style:normal;color:var(--orange);line-height:1}
.quote-open{top:-12px;left:0}
.quote-close{bottom:-38px;right:0}
.testimonial blockquote{padding:0 28px}

.about-title{position:absolute;top:1037px;left:0;right:0}
.about{position:absolute;top:1076px;left:142px;width:410px;display:flex;gap:28px;font-size:5px;line-height:8px;color:var(--body)}
.about p{flex:1}
.about-divider{position:absolute;top:1072px;left:558px;width:1px;height:80px;background:var(--line)}

.site-footer{position:absolute;bottom:0;left:0;right:0;height:32px;background:var(--footer);display:flex;align-items:center;padding:0 142px;font-size:5px;color:#999}
.footer-nav{display:flex;gap:14px;margin-left:auto;color:#ccc}
</style>
</head>
<body>
<header class="site-header">
  <div class="brand">Quarrix Diary</div>
  <div class="search">Search events</div>
  <nav class="main-nav"><span>EVENTS</span><span>CALENDAR</span><span>ADVERTISE</span><span>PREMIUM</span></nav>
  <div class="account"><span>LOGIN</span><span>REGISTER</span></div>
</header>

<section class="hero">
  <div class="hero-photo" role="img" aria-label="Concert audience facing a lit stage"></div>
  <div class="hero-content">
    <h1>WATCH SOME NEW</h1>
    <p>Browse the networking calendar, book your seat and meet local business people near you.</p>
    <span class="btn-primary">VIEW CALENDAR</span>
  </div>
</section>

<h2 class="section-title events-title">EVENTS</h2>
<section class="events">
  <div class="event-row">
    <div class="event-photo photo-crowd" role="img" aria-label="Crowd at an evening event"></div>
    <article class="event-card">
      <h2>ARTICLE TITLE</h2>
      <p>Thu 14 March, 6:30pm. A relaxed evening of introductions for founders, freelancers and local business owners. Premium listing: highlighted in the calendar and shown first in search. Book a seat from your subscriber area and add the date straight to your own diary.</p>
      <span class="btn-outline">LEARN MORE</span>
    </article>
  </div>
  <div class="event-row">
    <article class="event-card">
      <h2>ARTICLE TITLE</h2>
      <p>Every Tuesday, 8:00am. A weekly breakfast club for sales and marketing teams. Recurring events are a paid feature for subscribers, so organisers can post once and have each session appear in the calendar automatically, week after week.</p>
      <span class="btn-outline">LEARN MORE</span>
    </article>
    <div class="event-photo photo-stage" role="img" aria-label="Arena audience in front of a bright stage"></div>
  </div>
  <div class="event-row">
    <div class="event-photo photo-banquet" role="img" aria-label="Banquet hall with round dinner tables"></div>
    <article class="event-card">
      <h2>ARTICLE TITLE</h2>
      <p>Sat 23 March, 7:00pm. Annual awards dinner for the regional business community with guest speakers and table sponsors. Advertise your company on this page or in the ad spaces across the site, and reach members planning their next event.</p>
      <span class="btn-outline">LEARN MORE</span>
    </article>
  </div>
</section>

<h2 class="section-title how-title">HOW IT WORKS</h2>
<figure class="testimonial">
  <span class="quote-mark quote-open">&ldquo;</span>
  <blockquote>It is a long established fact that a reader will be distracted by the readable content of a page when looking at its layout. The point of using Lorem Ipsum is that it has a more-or-less normal distribution of letters, as opposed to using 'Content here, content here', making it look like readable English. Many desktop publishing packages and web page editors now use</blockquote>
  <span class="quote-mark quote-close">&rdquo;</span>
</figure>

<h2 class="section-title about-title">ABOUT US</h2>
<section class="about">
  <p>Quarrix Diary began as a simple shared calendar for local organisers and has grown into a full events resource. Visitors can browse by date, topic or area, save events to their own diary and get reminders before each session. Subscribers get a private client area where they add, edit and manage their own listings, see who is attending and download guest lists whenever they need them.</p>
  <p>Premium status puts your events at the top of the calendar with a highlighted card and badge. Businesses can book advert spaces across the site to reach an engaged local audience. If you already run an online diary on your own website, our API can import those events for you, so every listing stays in step without entering it twice. The site works just as well on phones and tablets.</p>
</section>
<div class="about-divider"></div>

<footer class="site-footer">
  <span>&copy; 2024 Quarrix Diary</span>
  <nav class="footer-nav"><span>CALENDAR</span><span>ADVERTISE</span><span>PREMIUM</span><span>CONTACT</span></nav>
</footer>
</body>
</html>
```